Home Security Company Business Card

Looking for a eye catching business card that is non traditional and stands out but yet still looks professional. It should include all the pertinent information such as name, title, address, telephone, e-mail, website address should definitely stand out and then finally the logo.

Target Market(s)

Residential and Commercial accounts mostly upscale accounts

Industry/Entity Type

Security

Contact Information for Business Card

Name
Title
Address
Office #
Cell #
E-mail
Website

Font styles to use
Serif
Sans Serif

Requirements
Must have
• Logo, two sided color configuration
Nice to have
• You decide
Should not have
• There really aren't any.

```html
<!DOCTYPE html>
<html lang="en">
<head>
<meta charset="utf-8">
<title>Ironvale Protection Group – Business Card</title>
<link rel="stylesheet" href="https://fonts.googleapis.com/css2?family=Open+Sans:wght@400;600;700&display=swap">
<style>
  :root {
    --maroon: #7a1418;
    --maroon-dark: #5e0d11;
    --gold: #e8b63a;
    --gold-soft: #f3d98a;
    --silver-light: #d9dbde;
    --silver-dark: #9ea2a8;
    --paper: #ffffff;
    --stage: #ecebe8;
    --ink-light: #ffffff;
  }
  * { box-sizing: border-box; margin: 0; padding: 0; }
  html, body { width: 1200px; height: 913px; overflow: hidden; }
  body {
    background: var(--stage);
    font-family: "Open Sans", Arial, sans-serif;
    position: relative;
  }
  .card {
    position: absolute;
    width: 525px;
    height: 300px;
    border-radius: 16px;
    overflow: hidden;
    box-shadow: 0 10px 28px rgba(0,0,0,0.18);
  }
  /* Front */
  .card-front {
    left: 50px; top: 306px;
    background: linear-gradient(160deg, var(--silver-light) 0%, #c3c6ca 55%, var(--silver-dark) 100%);
  }
  .front-band {
    position: absolute; left: 0; top: 0; bottom: 0; width: 78px;
    background: linear-gradient(180deg, var(--maroon) 0%, var(--maroon-dark) 100%);
  }
  .band-icons {
    position: absolute; left: 46px; top: 182px;
    display: flex; flex-direction: column; gap: 9px;
  }
  .band-icons svg { width: 16px; height: 16px; display: block; }
  .brand {
    position: absolute; left: 100px; top: 36px;
    display: flex; align-items: center; gap: 10px;
    color: var(--maroon);
    font-weight: 700;
    font-size: 20px;
    letter-spacing: 0.5px;
    text-transform: uppercase;
  }
  .brand-dot {
    width: 14px; height: 14px; border-radius: 50%;
    background: var(--gold);
  }
  .holder {
    position: absolute; left: 100px; top: 102px;
    color: var(--ink-light);
  }
  .holder-name { font-size: 28px; font-weight: 700; line-height: 1.1; text-shadow: 0 1px 2px rgba(0,0,0,0.25); }
  .holder-title { font-size: 15px; font-weight: 600; color: var(--gold); margin-top: 2px; }
  .contact-list {
    position: absolute; left: 100px; top: 178px;
    list-style: none;
    color: var(--ink-light);
    font-size: 15px;
    line-height: 25px;
    text-shadow: 0 1px 2px rgba(0,0,0,0.3);
  }
  /* Back */
  .card-back {
    left: 625px; top: 306px;
    background: var(--paper);
  }
  .back-band {
    position: absolute; right: 34px; top: 0; bottom: 0; width: 46px;
    background: linear-gradient(90deg, var(--gold-soft), var(--gold));
  }
  .back-brand {
    position: absolute; left: 0; right: 80px; top: 110px;
    display: flex; justify-content: center; align-items: center; gap: 12px;
    color: var(--maroon);
    font-weight: 700;
    font-size: 24px;
    letter-spacing: 0.5px;
    text-transform: uppercase;
  }
  .back-brand .brand-dot { width: 18px; height: 18px; }
  .website {
    position: absolute; left: 0; right: 80px; top: 222px;
    text-align: center;
    color: var(--maroon);
    font-weight: 700;
    font-size: 17px;
  }
</style>
</head>
<body>
  <section class="card card-front" aria-label="Business card front">
    <div class="front-band">
      <div class="band-icons">
        <svg viewBox="0 0 16 16" aria-hidden="true"><path d="M4 2l2.5 3-1.5 1.5c.8 1.8 2.2 3.2 4 4l1.5-1.5 3 2.5-1.5 2.5C7 13.5 2.5 9 1.5 3.5z" fill="none" stroke="var(--gold)" stroke-width="1.4" stroke-linejoin="round"/></svg>
        <svg viewBox="0 0 16 16" aria-hidden="true"><rect x="4.5" y="1.5" width="7" height="13" rx="1.5" fill="none" stroke="var(--gold)" stroke-width="1.4"/><circle cx="8" cy="12" r="0.9" fill="var(--gold)"/></svg>
        <svg viewBox="0 0 16 16" aria-hidden="true"><rect x="1.5" y="3.5" width="13" height="9" rx="1" fill="none" stroke="var(--gold)" stroke-width="1.4"/><path d="M1.5 4l6.5 5 6.5-5" fill="none" stroke="var(--gold)" stroke-width="1.4"/></svg>
        <svg viewBox="0 0 16 16" aria-hidden="true"><path d="M8 15s5-5.2 5-8.5A5 5 0 0 0 3 6.5C3 9.8 8 15 8 15z" fill="var(--gold)"/><circle cx="8" cy="6.5" r="1.8" fill="var(--maroon)"/></svg>
      </div>
    </div>
    <div class="brand"><span class="brand-dot"></span>Ironvale Protection Group</div>
    <div class="holder">
      <h1 class="holder-name">Daniel Marlowe</h1>
      <p class="holder-title">Owner</p>
    </div>
    <ul class="contact-list">
      <li>+555 0142-3381</li>
      <li>+5550198-27640</li>
      <li>info@danielmarlowemail.com</li>
      <li>742 Harbor Lane Millbrook, Ohio 40000</li>
    </ul>
  </section>

  <section class="card card-back" aria-label="Business card back">
    <div class="back-band"></div>
    <div class="back-brand"><span class="brand-dot"></span>Ironvale Protection Group</div>
    <p class="website">www.ironvaleprotectiongroup.com</p>
  </section>
</body>
</html>
```